Book Cover for Lantern Cousins Notes from the Orchard

We have written a book that brings together Notes from the Orchard from a variety of women's voices.
We developed a draft book cover that we like using Canva (attached below). We'd love a book cover that is similar to this image, but looks more professional.
Following are the themes we’d like to depict in the book cover, and in parentheses, how they are represented in the current cover:
1. Divinely feminine (overall cover)
2. Currents of enlightenment (the swirls of light carrying the butterfly)
3. Diversity (a myriad of colors)
4. The solo journey into the unknown (the single butterfly’s flight)
5. Buoyancy and joy (again, the dancing colors and floating butterfly)
6. Boldly feminine (the blue butterfly, set against brush strokes of light)
7. Homage to a dear friend (she loved blue butterflies, the cosmos - this butterfly has hints of the cosmos in her wings, and painting - this background has brush strokes of light).
Book Title, Subtitle, and Editor:
Lantern Cousins
Notes from the Orchard
Edited by Ilse Varno
Thank you very much for considering this project!
People who are interested in Women and Spirituality

```html
<!DOCTYPE html>
<html lang="en">
<head>
<meta charset="utf-8">
<title>Lantern Cousins: Notes from the Orchard</title>
<link rel="stylesheet" href="https://fonts.googleapis.com/css2?family=Cinzel:wght@400&family=Great+Vibes&display=swap">
<style>
  :root {
    --paper: #ffffff;
    --ink-blue: #1f3591;
    --magenta: #d3168c;
    --wing-light: #8fd0f7;
    --wing-mid: #5a98e8;
    --wing-dark: #141c3d;
    --spark: #4fb2dc;
  }
  html, body {
    margin: 0;
    padding: 0;
    overflow: hidden;
    background: var(--paper);
  }
  .cover {
    position: relative;
    width: 752px;
    height: 1200px;
    background: var(--paper);
    overflow: hidden;
    font-family: "Cinzel", "Times New Roman", serif;
  }
  .series-title {
    position: absolute;
    top: 32px;
    left: 0;
    width: 752px;
    margin: 0;
    text-align: center;
    font-weight: 400;
    font-size: 47px;
    line-height: 1;
    letter-spacing: 9px;
    color: var(--ink-blue);
  }
  .butterfly-art {
    position: absolute;
    left: 204px;
    top: 122px;
    width: 536px;
    height: 534px;
    background:
      radial-gradient(ellipse 46% 52% at 52% 48%, var(--wing-light) 0%, var(--wing-mid) 45%, var(--wing-dark) 85%, rgba(20,28,61,0) 100%);
    border-radius: 50%;
    opacity: 0.92;
  }
  .spark-trail {
    position: absolute;
    left: 10px;
    top: 590px;
    width: 440px;
    height: 210px;
    background: radial-gradient(ellipse 50% 50% at 50% 50%, rgba(79,178,220,0.22) 0%, rgba(79,178,220,0) 100%);
  }
  .book-title {
    position: absolute;
    top: 862px;
    left: 54px;
    width: 650px;
    margin: 0;
    font-weight: 400;
    color: var(--magenta);
  }
  .book-title .line {
    display: block;
    line-height: 1;
  }
  .book-title .line-one {
    font-size: 92px;
    letter-spacing: 14px;
    white-space: nowrap;
  }
  .book-title .joiner {
    font-family: "Great Vibes", cursive;
    font-size: 76px;
    letter-spacing: 0;
    margin-left: -4px;
  }
  .book-title .line-two {
    margin-top: 30px;
    font-size: 72px;
    letter-spacing: 33px;
  }
  .editor {
    position: absolute;
    top: 1102px;
    left: 0;
    width: 752px;
    margin: 0;
    text-align: center;
    font-size: 36px;
    line-height: 1;
    letter-spacing: 12px;
    color: var(--ink-blue);
  }
</style>
</head>
<body>
  <main class="cover">
    <h2 class="series-title">LANTERN COUSINS</h2>
    <div class="spark-trail" role="img" aria-label="Trail of small blue sparkles drifting behind the butterfly"></div>
    <div class="butterfly-art" role="img" aria-label="Illustration of a single luminous blue butterfly with cosmic, starlit wings"></div>
    <h1 class="book-title">
      <span class="line line-one">NOTES<span class="joiner">from the</span></span>
      <span class="line line-two">ORCHARD</span>
    </h1>
    <p class="editor">EDITED BY ILSE VARNO</p>
  </main>
</body>
</html>
```